A clean crisp business card for a Landscape Construction company. Designed to be easy to read contact/ info and also be appealing/interesting, unlike a traditional business card.

Industry/Entity Type

Landscape Construction

Contact Information for Business Card

Company name : Brambleford Landscape Construction, phone number: (877) 62Vista, website:Bramblefordyards.example, Email, sales@bramblefordyards.example

Requirements
Nice to have
• Luxurious finishes/ details…. Icons or emblems next to contact info
Should not have
• Clipart or general pictures

```html
<!DOCTYPE html>
<html lang="en">
<head>
<meta charset="utf-8">
<title>Brambleford Landscape Construction – Business Card</title>
<link rel="stylesheet" href="https://fonts.googleapis.com/css2?family=Cinzel:wght@400;600&display=swap">
<style>
  :root {
    --bg: #0b0b0b;
    --card: #151515;
    --lime: #9ccc2c;
    --blue: #1f6fd1;
    --rule: #3a3a3a;
    --emboss: #4e4e4e;
    --serif: "Cinzel", "Trajan Pro", serif;
  }
  * { margin: 0; padding: 0; box-sizing: border-box; }
  html, body {
    width: 1200px; height: 820px; overflow: hidden;
    background: var(--bg);
    font-family: var(--serif);
  }
  .sheet {
    width: 1200px; height: 820px;
    display: flex; align-items: center; justify-content: center; gap: 40px;
  }
  .card {
    position: relative;
    width: 540px; height: 309px;
    background: var(--card);
    border-left: 3px solid var(--lime);
    border-bottom: 3px solid var(--lime);
    box-shadow: 0 18px 40px rgba(0,0,0,.7);
    text-transform: uppercase;
  }
  /* front */
  .brand {
    position: absolute; top: 40px; right: 36px;
    display: flex; align-items: center; gap: 12px;
  }
  .brand-dot {
    width: 28px; height: 28px; border-radius: 50%;
    background: var(--lime);
  }
  .brand-name {
    color: var(--blue); font-weight: 600; font-size: 26px;
    line-height: 1.1; letter-spacing: 1px;
  }
  .brand-name small { display: block; font-size: 11px; letter-spacing: 3px; }
  .person { position: absolute; left: 36px; right: 30px; top: 128px; }
  .person-row { display: flex; align-items: baseline; gap: 12px; }
  .person-name {
    font-size: 23px; font-weight: 600; color: var(--blue);
    letter-spacing: .5px; white-space: nowrap;
  }
  .person-name span { color: var(--lime); }
  .divider { flex: 1; height: 1px; background: var(--rule); }
  .person-role { font-size: 13px; color: var(--lime); letter-spacing: 1px; margin-top: 4px; }
  .contacts { position: absolute; left: 36px; bottom: 26px; list-style: none; }
  .contacts li {
    display: flex; align-items: center; gap: 10px;
    font-size: 12px; color: var(--lime); letter-spacing: .6px; line-height: 22px;
  }
  .contacts svg { width: 14px; height: 14px; fill: var(--blue); flex: none; }
  .contacts .web { color: var(--blue); }
  .address {
    position: absolute; right: 30px; top: 176px; text-align: right;
    font-style: normal;
    font-size: 12px; color: var(--lime); letter-spacing: .6px; line-height: 18px;
  }
  /* back */
  .card-back { display: flex; align-items: center; justify-content: center; }
  .back-name {
    text-align: center; color: var(--emboss); font-weight: 600;
    font-size: 38px; letter-spacing: 2px; line-height: 1.2;
  }
  .back-name small { display: block; font-size: 14px; letter-spacing: 5px; }
</style>
</head>
<body>
<main class="sheet">
  <section class="card card-front">
    <div class="brand">
      <span class="brand-dot"></span>
      <p class="brand-name">Brambleford<small>Landscape Construction</small></p>
    </div>
    <div class="person">
      <div class="person-row">
        <p class="person-name">Daniel <span>Hartwell</span></p>
        <span class="divider"></span>
      </div>
      <p class="person-role">Managing Director</p>
    </div>
    <ul class="contacts">
      <li><svg viewBox="0 0 24 24"><path d="M6.6 10.8a15 15 0 0 0 6.6 6.6l2.2-2.2c.3-.3.7-.4 1-.2 1.1.4 2.3.6 3.6.6.6 0 1 .4 1 1V20c0 .6-.4 1-1 1A17 17 0 0 1 3 4c0-.6.4-1 1-1h3.5c.6 0 1 .4 1 1 0 1.3.2 2.5.6 3.6.1.3 0 .7-.2 1z"/></svg>(877) 62Vista</li>
      <li><svg viewBox="0 0 24 24"><path d="M2 5h20v14H2zm2 2v.5l8 5 8-5V7l-8 5z"/></svg>sales@bramblefordyards.example</li>
      <li class="web"><svg viewBox="0 0 24 24"><path d="M12 2a10 10 0 1 0 0 20 10 10 0 0 0 0-20zm6.9 6h-3a15 15 0 0 0-1.3-3.9A8 8 0 0 1 18.9 8zM12 4c.8 1.2 1.5 2.5 1.9 4h-3.8c.4-1.5 1.1-2.8 1.9-4zM4.3 14a8 8 0 0 1 0-4h3.4a16 16 0 0 0 0 4zm.8 2h3a15 15 0 0 0 1.3 3.9A8 8 0 0 1 5.1 16zm3-8h-3a8 8 0 0 1 4.3-3.9C8.8 5.3 8.4 6.6 8.1 8zM12 20c-.8-1.2-1.5-2.5-1.9-4h3.8c-.4 1.5-1.1 2.8-1.9 4zm2.3-6H9.7a14 14 0 0 1 0-4h4.6a14 14 0 0 1 0 4zm.3 5.9c.6-1.2 1-2.5 1.3-3.9h3a8 8 0 0 1-4.3 3.9zM16.3 14a16 16 0 0 0 0-4h3.4a8 8 0 0 1 0 4z"/></svg>Bramblefordyards.example</li>
    </ul>
    <address class="address">
      418, Fernhollow Lane<br>Greenway Park Suite 3<br>60817, Valemont
    </address>
  </section>

  <section class="card card-back">
    <p class="back-name">Brambleford<small>Landscape Construction</small></p>
  </section>
</main>
</body>
</html>
```